RWT Fittings Ltd Business Cards

We need a business card with our business logo. We provide window and door installations on high-rises in west coast British Colombia, Canada.

I would like my business information and details on one side of the card, and the other side the company name with logo

Target Market(s)

General Contractors

Industry/Entity Type

Construction

Contact Information for Business Card

one side i want my company name and logo in the dark theme logo that i provided

Requirements
Must have
• Marco Peltieri, 16045518293, RWTFittings@mailbox-demo.com, 1407-5194 Linden Row Burnaby BC, V5H 2K9, Owner & Manager

```html
<!DOCTYPE html>
<html lang="en">
<head>
<meta charset="utf-8">
<title>RWT Fittings Ltd – Business Cards</title>
<link href="https://fonts.googleapis.com/css2?family=Open+Sans:wght@400;600;700&display=swap" rel="stylesheet">
<style>
  :root {
    --stage: #232323;
    --card: #ffffff;
    --brand-blue: #29a8e0;
    --panel-grey: #9b9b9b;
    --text-white: #ffffff;
  }
  * { box-sizing: border-box; margin: 0; padding: 0; }
  html, body {
    width: 1200px; height: 780px; overflow: hidden;
    background: var(--stage);
    font-family: "Open Sans", Arial, sans-serif;
  }
  .stage { position: relative; width: 1200px; height: 780px; }

  .card {
    position: absolute;
    width: 560px; height: 320px;
    background: var(--card);
    border-radius: 24px;
    border-bottom: 3px solid var(--brand-blue);
    border-left: 2px solid var(--brand-blue);
    overflow: hidden;
  }
  .card--front { left: 80px; top: 60px; }
  .card--back  { left: 560px; top: 410px; }

  .brand {
    display: flex; align-items: center; gap: 14px;
    color: var(--brand-blue);
    font-weight: 700;
    white-space: nowrap;
  }
  .brand__mark { background: var(--brand-blue); flex: none; }

  .card--front .brand {
    position: absolute; inset: 0; justify-content: center;
    font-size: 44px;
  }
  .card--front .brand__mark { width: 34px; height: 34px; }

  .card--back .brand {
    position: absolute; left: 30px; top: 0; height: 100%;
    font-size: 22px; gap: 10px;
  }
  .card--back .brand__mark { width: 18px; height: 18px; }

  .info-panel {
    position: absolute; inset: 0;
    background: var(--panel-grey);
    clip-path: polygon(46% 0, 100% 0, 100% 100%, 58% 100%);
  }
  .contact {
    position: absolute; left: 335px; top: 52px;
    padding-left: 14px;
    border-left: 2px solid var(--brand-blue);
    color: var(--text-white);
    font-size: 11.5px; line-height: 1.6;
    white-space: nowrap;
  }
  .contact__name {
    color: var(--brand-blue); font-weight: 700;
    font-size: 18px; text-transform: uppercase; line-height: 1.2;
  }
  .contact__role { font-size: 13px; margin-bottom: 10px; }
  .contact__row { display: flex; align-items: center; gap: 6px; }
  .contact__icon { width: 12px; height: 12px; flex: none; }
  .contact__address { margin-top: 12px; font-size: 12px; }
</style>
</head>
<body>
<main class="stage">
  <section class="card card--front" aria-label="Business card front">
    <div class="brand"><span class="brand__mark"></span>RWT Fittings Ltd</div>
  </section>

  <section class="card card--back" aria-label="Business card back">
    <div class="brand"><span class="brand__mark"></span>RWT Fittings Ltd</div>
    <div class="info-panel"></div>
    <div class="contact">
      <p class="contact__name">Marco Peltieri</p>
      <p class="contact__role">Owner &amp; Manager</p>
      <p class="contact__row">
        <svg class="contact__icon" viewBox="0 0 24 24"><path fill="#29a8e0" d="M6.6 10.8a15 15 0 0 0 6.6 6.6l2.2-2.2c.3-.3.7-.4 1-.2 1.1.4 2.3.6 3.6.6.6 0 1 .4 1 1V20c0 .6-.4 1-1 1A17 17 0 0 1 3 4c0-.6.4-1 1-1h3.5c.6 0 1 .4 1 1 0 1.3.2 2.5.6 3.6.1.3 0 .7-.2 1z"/></svg>
        16045518293
      </p>
      <p class="contact__row">
        <svg class="contact__icon" viewBox="0 0 24 24"><path fill="#29a8e0" d="M2 5h20v14H2zm2 2v.5l8 5 8-5V7z"/></svg>
        RWTFittings@mailbox-demo.com
      </p>
      <p class="contact__row">
        <svg class="contact__icon" viewBox="0 0 24 24"><circle cx="12" cy="12" r="9" fill="none" stroke="#29a8e0" stroke-width="2.5"/><path d="M3 12h18M12 3c3 3 3 15 0 18M12 3c-3 3-3 15 0 18" fill="none" stroke="#29a8e0" stroke-width="2"/></svg>
        www.rwtfittings-demo.com
      </p>
      <p class="contact__address">1407-5194 Linden Row<br>Burnaby BC, V5H 2K9</p>
    </div>
  </section>
</main>
</body>
</html>
```